Mobile Repair Service on location needs a Web Design

We are starting a new mobile device repair service called Handset Haven and our website needs a design!

Hello Designers!
First, we'd like to make clear this is more than a simple web design contest, we want the designers to create an idea. We want someone who can create the whole theme of the service's we provide. We want someone that can help design our visual branding, help us communicate a sentiment. And we are willing to pay for that.

Who are we?
Our company is based in Rotterdam, the Netherlands. We provide different services for all kinds of electronic devices. The kind of services we provide are, among other things, installations of hardware and software and the repair of broken or malfunctioning devices.
We are starting a new service that offers mobile device repairs on location, be it at the home of our customers, their office, or any other place. Just give us the address and we will come to you for the repair job. This is also our main USP. We have multiple skilled engineers who drive trough the country on a daily basis and can be on location within a working day. Repair is done immediately onsite while the customer waits. At this stage we will start with the smartphone product-group within the mobile devices. In a second phase we might also add tablets.
People don't want to be without their phone for weeks because of some parts that needed to be ordered by a repair center they had to sent their phone to. We offer a fully functional mobile repair center in the form of specially customized vans. These vans have all the tools and utilities needed by our engineers to safely repair your mobile device. Your phone is being repaired directly in front of you, the next business-day, on a location you desire.

For this new service we are creating a website called Handset Haven. The website needs a story and matching design and this is where you come in. We are not looking for a simple template design we can get from any place. We need a story. We want you to create an idea, build a unique theme or vision that helps sell the product/service. This goes beyond the design of the website. We need the whole package, the design you are creating needs to have returning elements like icons, color use, images, maybe even characters etc. You name it! There needs to be a common thread in the design so we can reuse elements in, for example, the email templates, the work order or receipt we give to our customers (we may contact the winner of the contest to design these for us as well!).

The name 'Handset Haven' is chosen. Rehab (short for rehabilitate) has a bold and playful tone to it and the design needs to reflect the name. So we're looking for a somewhat playful and cheeky design. Definitely not too serious and definitely modern. We already got a logo that we love and that fit's this description (see attached design documents for the logo). It's bold, powerful and fun. Our web design needs to reflect this as well and has to fit in with our logo.
We would really like it if the design somehow incorporates elements that highlight our unique selling points (repairs on location, we come to you etc.). We would really like some form of story telling in the design. Think clumsy people breaking their phones. Teenagers in tears because they have no access to their friends. People nowadays have the need to always be 'connected'. What happens when your phone is broken or malfunctioning? We're handling tech, we are nerds and a little bit weird, but we're professionals and here to help you with your problem. The sentiment Byte Brigade tries to communicate is something we really like. We're looking for fresh idea's, anything goes!

In an overview all Unique Selling Points of the Handset haven service:
- Professional service on location. Don’t ship to us we will come to you!
- Clear pricing upfront. No hidden cost.
- Next business-day repair.
- Backed by a professional call center open 12 hours a day and open on a Saturday as well
- Backed by a professional repair center with more then 12 years of experience
- Repair is done by certified engineers
- 1 year warranty on the repair

The process:
The main function of our website will be for customers to make a repair request. A customer will visit our website and can make a repair request immediately by going through a 'request-order-flow'. In this flow he or she will need to fill in some forms and can select wich type/model/brand of mobile device he or she has and what parts need to be repaired. After a request is placed we will call the customer back (within an hour) for a short intake and to set a date/time and location. Our engineer will meet the customer at the specified location and will repair the device onsite in one of our mobile repair centers, which is a specialized van equipped with all the tools needed for device restorations.
So in short the steps are:
- Choose your device and repair job
- Place the order
- Get a callback within the hour
- Set date and location
- We will come to you.

Website functionality:
Our website is our main form of communication. So the sentiment we want to communicate needs be reflected in the design. We need a main/front page designed (preferably a long scrolling page design) containing:
1. Customers will be able to request a repair job directly on our website. So there will need to be a prominent button/link at the top of our main page that will bring the customer to this 'request-order-flow'. This is the main flow which needs to be full focus on the front page. All other items are secondary.
2. The general information of who we are and what we do, and why the customer should choose us. Preferably in short bullet-point type keywords/sentences with icons or other visual cues. See our unique selling points to get an idea of the information that will be displayed here.
3. There needs to be a section that will explain the process (see above) of a repair request step-by- step, again in brief short key sentences and with (custom) icons.
4. There needs to be a section that explains to the customer he/she can always contact us if they are not sure what the problem is with their device, and for this reason are not sure what repair request they should order.
5. We want to implement some functionality that display customer ratings or customer reviews. So there needs to be room for some kind of widget of plugin we're going to implement which shows these reviews.
6. A 'For business section' where we will explain all the options we provide for corporate clients.
7. Social media links.
8. There needs to be a menu with buttons that leads to the all sections described in the previous points.

For now, we need a design for our front page. In the second phase, when we have picked our winner, we may ask the winner to design the page(s) for our request workflow as well.

EDIT:
Finally, we have a very specific order in mind for the different segments of our website. We would like you to add some more segments that were not in our original brief as well:

1. Top header with order/request button. (should instantly make clear our main USP, we do repairs on location)
2. Our process
3. Our unique selling points / why choose us
4. The kind of repairs we do (broken screens, broken batteries, water damage, broken camera's, no sound etc.)
5. A 'meet our team' section, where we introduce some of our engineers
6. A 'contact us for any questions' section/
7. Testimonials/user reviews
8. A section where we show key performance indicators
9. 'For businesses' sections
10.'Subscribe for newsletter' field
11. Social media buttons

Industry/Entity Type

It Service

Number of Pages Required

1 page

Font styles to use
Sans Serif

Requirements
Must have
• a main/front page, design only
• custom icons/images for banners, adverts online and in print (high res)
Nice to have
• Storytelling in our design.
• Design that fits with our brand new logo.
• Elements like icons to have a flat design.
• Keep in mind that the website will need to be responsive when designing! (Ideally provide an example of the mobile design as well)
• Create a fun and trustworthy feeling.

```html
<!DOCTYPE html>
<html lang="en">
<head>
<meta charset="utf-8">
<title>Handset Haven – We will come to you</title>
<link href="https://fonts.googleapis.com/css2?family=Nunito+Sans:wght@400;600;700;800;900&family=Open+Sans:wght@400;600;700&display=swap" rel="stylesheet">
<style>
:root{
  --orange:#ef6a2f;
  --orange-deep:#e35f25;
  --navy:#5a73a8;
  --icon-blue:#4f6aa1;
  --ink:#1f1f1f;
  --body:#555a60;
  --muted:#8a8f96;
  --line:#d9dce1;
  --pale:#eef1f8;
  --white:#ffffff;
  --hero-a:#9a9a9a;
  --hero-b:#cfcfcf;
}
*{box-sizing:border-box;margin:0;padding:0}
html,body{width:1200px;height:2769px;overflow:hidden;background:var(--white)}
body{position:relative;font-family:"Open Sans",Arial,sans-serif;color:var(--body)}
.abs{position:absolute}
.heading{font-family:"Nunito Sans",Arial,sans-serif;font-weight:800;color:var(--ink)}

/* header */
.site-header{position:absolute;left:0;top:0;width:1200px;height:111px}
.brand{left:96px;top:18px;display:flex;align-items:center;gap:16px}
.brand-dot{width:62px;height:62px;border-radius:50%;background:var(--orange)}
.brand-name{font-family:"Nunito Sans",Arial,sans-serif;font-weight:900;font-size:27px;line-height:26px;color:#2a2a2a;text-transform:uppercase}
.brand-tag{left:178px;top:78px;font-family:"Nunito Sans",sans-serif;font-weight:700;font-size:11px;color:var(--navy)}
.util-links{right:98px;top:20px;display:flex;gap:10px;font-size:11.5px;color:#444}
.util-links span.sep{color:#bbb}
.util-links .ico{display:inline-block;width:8px;height:8px;border-radius:50%;background:var(--orange);margin-right:5px;vertical-align:0}
.call{left:584px;top:56px;display:flex;align-items:center;gap:12px;font-size:14px;color:#333}
.call-ring{width:34px;height:34px;border:1.5px solid #bbb;border-radius:50%;display:flex;align-items:center;justify-content:center}
.call b{font-size:19px;font-weight:700;color:#222;margin-left:4px}
.cart{left:884px;top:56px;display:flex;align-items:center;gap:10px;font-size:13px}
.cart b{font-weight:700;color:#222;font-size:14px}
.cart span{color:var(--muted);font-size:11.5px}

/* nav */
.main-nav{position:absolute;left:0;top:111px;width:1200px;height:42px;background:var(--navy)}
.main-nav a{position:absolute;top:11px;font-family:"Nunito Sans",sans-serif;font-weight:700;font-size:15px;color:var(--white);text-decoration:none}
.main-nav a.active{color:#ff8b55}
.search{position:absolute;left:740px;top:5px;width:360px;height:33px;border-radius:17px;background:var(--white);padding:0 18px;display:flex;align-items:center;justify-content:space-between;font-size:13px;color:#999}

/* hero */
.hero{position:absolute;left:0;top:153px;width:1200px;height:441px;background:linear-gradient(180deg,var(--hero-b),var(--hero-a))}
.hero-screens{position:absolute;left:330px;top:70px;width:540px;height:371px;background:linear-gradient(90deg,#6f7f86,#3d6f7f 40%,#5f8f9c 60%,#7c8b90);opacity:.55;border-radius:30px 30px 0 0}
.hero-arrow{position:absolute;top:194px;width:45px;height:52px;border:1px solid rgba(255,255,255,.7);background:rgba(255,255,255,.15);display:flex;align-items:center;justify-content:center}
.hero-kicker{position:absolute;left:0;width:1200px;top:122px;text-align:center;font-family:"Nunito Sans",sans-serif;font-weight:600;font-size:31px;color:var(--white)}
.hero-title{position:absolute;left:0;width:1200px;top:164px;text-align:center;font-family:"Nunito Sans",sans-serif;font-weight:900;font-size:61px;color:var(--white);letter-spacing:.5px;text-shadow:0 2px 6px rgba(0,0,0,.25)}
.locator{position:absolute;left:364px;top:255px;width:417px;height:46px;background:var(--white);display:flex;align-items:center;padding:0 16px;gap:12px;font-size:13px;color:#888}
.locator .chev{margin-left:auto}
.go{position:absolute;left:781px;top:255px;width:54px;height:46px;background:var(--orange);color:var(--white);font-weight:700;font-size:15px;display:flex;align-items:center;justify-content:center}

/* welcome */
.welcome-title{left:100px;top:658px;font-size:29px}
.welcome-copy{left:100px;top:716px;width:470px;font-size:12.5px;line-height:27px;color:var(--body)}
.welcome-copy p+p{margin-top:27px}
.read-more{left:100px;top:929px;width:135px;height:38px;border:1.5px solid #c9c9c9;border-radius:19px;display:flex;align-items:center;justify-content:center;font-size:12px;font-weight:700;color:var(--orange)}
.video{left:628px;top:672px;width:474px;height:288px;border:1px solid #ccc;padding:5px;background:var(--white)}
.video-still{width:100%;height:100%;background:linear-gradient(135deg,#dfe4ea,#b8c0c8 55%,#3b3f44);position:relative}
.play{position:absolute;left:50%;top:50%;width:64px;height:64px;margin:-32px 0 0 -32px;border-radius:50%;background:rgba(30,30,30,.85);display:flex;align-items:center;justify-content:center}
.rule{left:100px;top:1006px;width:1002px;height:1px;background:var(--line)}

/* why */
.section-title{position:absolute;left:0;width:1200px;text-align:center;font-size:28px}
.usp{position:absolute;width:340px;margin-left:-170px;text-align:center}
.usp svg{display:block;margin:0 auto}
.usp p{margin-top:14px;font-size:16.5px;line-height:27px;color:#222;font-weight:600}

/* how */
.how{position:absolute;left:0;top:1529px;width:1200px;height:387px;background:var(--pale)}
.step{position:absolute;width:210px;margin-left:-105px;text-align:center}
.step svg{display:block;margin:0 auto}
.step p{margin-top:20px;font-size:15.5px;line-height:26px;font-weight:600;color:#222}
.dash{position:absolute;top:155px}

/* promo */
.promo-photo{position:absolute;left:0;top:1916px;width:600px;height:488px;background:linear-gradient(160deg,#e9ecef,#c9d0d8 45%,#3a5fa8 70%,#26334c)}
.promo{position:absolute;left:600px;top:1916px;width:600px;height:488px;background:linear-gradient(120deg,var(--orange),var(--orange-deep))}
.promo h2{position:absolute;left:61px;top:50px;font-family:"Nunito Sans",sans-serif;font-weight:800;font-size:29px;line-height:41px;color:var(--white)}
.promo .lead{position:absolute;left:61px;top:142px;width:470px;font-size:14px;line-height:27px;color:#fde3d6}
.perk{position:absolute;left:61px;display:flex;align-items:center;gap:26px}
.perk-ring{width:92px;height:92px;border:1.5px solid rgba(255,255,255,.85);border-radius:50%;display:flex;align-items:center;justify-content:center}
.perk p{font-family:"Nunito Sans",sans-serif;font-weight:700;font-size:21px;line-height:28px;color:var(--white)}

/* footer */
.footer-col{position:absolute;top:2466px}
.footer-col h3{font-family:"Nunito Sans",sans-serif;font-weight:700;font-size:18px;color:#222;margin-bottom:14px}
.footer-col li{list-style:none;font-size:12px;line-height:27px;color:#555}
.vline{position:absolute;top:2466px;width:1px;height:170px;background:#e4e4e4}
.newsletter-note{font-size:12px;color:#555;margin-bottom:14px}
.subscribe{display:flex}
.subscribe .field{width:231px;height:36px;border:1px solid #ccc;font-size:11.5px;color:#777;padding:0 12px;display:flex;align-items:center}
.subscribe .btn{width:94px;height:36px;background:var(--orange);color:var(--white);font-size:12px;font-weight:700;display:flex;align-items:center;justify-content:center}
.social{display:flex;gap:8px;margin-top:10px}
.social i{display:block;width:34px;height:34px;border-radius:50%}
.copyright{position:absolute;left:0;top:2699px;width:1200px;height:70px;border-top:1px solid #e1e1e1;text-align:center;padding-top:22px;font-size:11.5px;color:#555}
</style>
</head>
<body>

<header class="site-header">
  <div class="abs brand"><span class="brand-dot"></span><span class="brand-name">Handset<br>Haven</span></div>
  <div class="abs brand-tag">We will come to you!</div>
  <nav class="abs util-links">
    <span><i class="ico"></i>Store Locator</span><span class="sep">|</span>
    <span><i class="ico"></i>Gift Cards</span><span class="sep">|</span>
    <span><i class="ico"></i>Wishlist</span><span class="sep">|</span>
    <span><i class="ico"></i>My Account</span><span class="sep">|</span>
    <span><i class="ico"></i>Login</span>
  </nav>
  <div class="abs call">
    <span class="call-ring"><svg width="16" height="16" viewBox="0 0 24 24"><path fill="#ef6a2f" d="M6.6 10.8a15 15 0 0 0 6.6 6.6l2.2-2.2c.3-.3.7-.4 1-.2 1.1.4 2.3.6 3.6.6.6 0 1 .4 1 1V20c0 .6-.4 1-1 1A17 17 0 0 1 3 4c0-.6.4-1 1-1h3.5c.6 0 1 .4 1 1 0 1.3.2 2.5.6 3.6.1.3 0 .7-.2 1z"/></svg></span>
    <span>Call us on:<b>1 800 555 0142</b></span>
  </div>
  <div class="abs cart">
    <svg width="34" height="30" viewBox="0 0 34 30"><path d="M1 3h6l4 17h17l4-12H9" fill="none" stroke="#ef6a2f" stroke-width="2.5" stroke-linejoin="round"/><circle cx="13" cy="26" r="2.5" fill="#ef6a2f"/><circle cx="26" cy="26" r="2.5" fill="#ef6a2f"/></svg>
    <b>My Cart</b><span>0 item(s) | $ 0.00 ▾</span>
  </div>
</header>

<nav class="main-nav">
  <a class="active" style="left:100px">Home</a>
  <a style="left:177px">About Us</a>
  <a style="left:279px">Services</a>
  <a style="left:373px">Products</a>
  <a style="left:471px">Brands</a>
  <a style="left:556px">Deals</a>
  <a style="left:635px">Contact</a>
  <div class="search">Search<svg width="14" height="14" viewBox="0 0 14 14"><circle cx="6" cy="6" r="4.5" fill="none" stroke="#888" stroke-width="1.6"/><path d="M9.5 9.5L13 13" stroke="#888" stroke-width="1.6"/></svg></div>
</nav>

<section class="hero" role="img" aria-label="Two smartphones with cracked screens on a grey concrete background">
  <div class="hero-screens"></div>
  <div class="hero-arrow" style="left:18px"><svg width="12" height="20" viewBox="0 0 12 20"><path d="M10 2L2 10l8 8" fill="none" stroke="#fff" stroke-width="2"/></svg></div>
  <div class="hero-arrow" style="left:1137px"><svg width="12" height="20" viewBox="0 0 12 20"><path d="M2 2l8 8-8 8" fill="none" stroke="#fff" stroke-width="2"/></svg></div>
  <div class="hero-kicker">Handset Haven</div>
  <h1 class="hero-title">WE WILL COME TO YOU</h1>
  <div class="locator"><svg width="11" height="15" viewBox="0 0 12 16"><path d="M6 0a6 6 0 0 0-6 6c0 4.5 6 10 6 10s6-5.5 6-10a6 6 0 0 0-6-6zm0 8.2A2.2 2.2 0 1 1 6 3.8a2.2 2.2 0 0 1 0 4.4z" fill="#777"/></svg>Choose Your Location<span class="chev">⌄</span></div>
  <div class="go">GO</div>
</section>

<h2 class="abs heading welcome-title">WELCOME TO HANDSET HAVEN</h2>
<div class="abs welcome-copy">
  <p>Our company is based in Rotterdam, the Netherlands. We provide different services for all kinds of electronic devices.</p>
  <p>The kind of services we provide are, among other things, installations of hardware and software and the repair of broken or malfunctioning devices. We are starting a new service that offers mobile device repairs on location, be it at the home of our customers, their office, or any other place.</p>
</div>
<div class="abs read-more">READ MORE &gt;&gt;</div>
<div class="abs video">
  <div class="video-still" role="img" aria-label="Video still of gloved hands repairing an opened smartphone">
    <div class="play"><svg width="22" height="24" viewBox="0 0 22 24"><path d="M3 2l17 10L3 22z" fill="#fff"/></svg></div>
  </div>
</div>
<div class="abs rule"></div>

<h2 class="section-title heading" style="top:1050px">WHY REAPIR AT HANDSET HAVEN</h2>

<div class="usp" style="left:247px;top:1138px">
  <svg width="40" height="54" viewBox="0 0 24 32"><path d="M12 0A12 12 0 0 0 0 12c0 9 12 20 12 20s12-11 12-20A12 12 0 0 0 12 0zm0 16.5a4.5 4.5 0 1 1 0-9 4.5 4.5 0 0 1 0 9z" fill="var(--orange)"/></svg>
  <p>Professional service on location. Don’t<br>ship to us we will come to you!</p>
</div>
<div class="usp" style="left:600px;top:1138px">
  <svg width="70" height="54" viewBox="0 0 70 54"><rect x="3" y="8" width="64" height="38" fill="none" stroke="var(--orange)" stroke-width="5"/><rect x="11" y="15" width="48" height="24" fill="var(--orange)"/><circle cx="35" cy="27" r="9" fill="#fff"/><text x="35" y="32" text-anchor="middle" font-family="Nunito Sans,sans-serif" font-weight="800" font-size="13" fill="var(--orange)">1</text></svg>
  <p>Clear pricing upfront.<br>No hidden cost.</p>
</div>
<div class="usp" style="left:951px;top:1138px">
  <svg width="58" height="54" viewBox="0 0 58 58"><path d="M50 4a14 14 0 0 0-17 17L4 50a4 4 0 0 0 6 6l29-29a14 14 0 0 0 17-17l-8 8-7-2-2-7z" fill="var(--orange)"/></svg>
  <p>Next business-day<br>repair</p>
</div>
<div class="usp" style="left:247px;top:1323px">
  <svg width="60" height="56" viewBox="0 0 60 56"><rect x="2" y="24" width="12" height="30" fill="var(--orange)"/><path d="M18 26l12-22c5 0 8 4 6 10l-2 8h18c4 0 6 4 4 7l-6 22c-1 3-3 5-6 5H18z" fill="var(--orange)"/></svg>
  <p>1 year warranty on the<br>repair</p>
</div>
<div class="usp" style="left:600px;top:1323px">
  <svg width="72" height="62" viewBox="0 0 72 62"><circle cx="14" cy="14" r="9" fill="var(--orange)"/><circle cx="58" cy="14" r="9" fill="var(--orange)"/><circle cx="36" cy="12" r="11" fill="var(--orange)"/><path d="M0 44c0-11 6-17 14-17s10 4 10 4v13z" fill="var(--orange)"/><path d="M72 44c0-11-6-17-14-17s-10 4-10 4v13z" fill="var(--orange)"/><path d="M16 60c0-17 8-26 20-26s20 9 20 26z" fill="var(--orange)"/></svg>
  <p>Repair is done by certified<br>engineers</p>
</div>
<div class="usp" style="left:951px;top:1323px">
  <svg width="60" height="58" viewBox="0 0 24 23"><path d="M12 0l3.7 7.6 8.3 1.2-6 5.8 1.4 8.4L12 19l-7.4 4 1.4-8.4-6-5.8 8.3-1.2z" fill="var(--orange)"/></svg>
  <p>Professional repair center with more<br>then 12 years of experience</p>
</div>

<section class="how">
  <h2 class="section-title heading" style="top:50px">HOW IT WORKS</h2>

  <div class="step" style="left:168px;top:140px">
    <svg width="62" height="102" viewBox="0 0 62 102"><rect x="14" y="2" width="46" height="86" rx="5" fill="none" stroke="var(--icon-blue)" stroke-width="4"/><rect x="2" y="12" width="46" height="88" rx="5" fill="var(--pale)" stroke="var(--icon-blue)" stroke-width="4"/><rect x="8" y="24" width="34" height="62" fill="var(--icon-blue)"/></svg>
    <p>Choose your device<br>and repair job</p>
  </div>
  <div class="step" style="left:391px;top:140px">
    <svg width="62" height="102" viewBox="0 0 62 102"><rect x="2" y="2" width="52" height="98" rx="6" fill="var(--icon-blue)"/><rect x="8" y="16" width="40" height="66" fill="var(--pale)"/><circle cx="28" cy="91" r="4" fill="var(--pale)"/><path d="M22 44l6-8 6 8" fill="none" stroke="var(--icon-blue)" stroke-width="2.5"/><path d="M13 44h40l-5 22H18z" fill="var(--pale)" stroke="var(--icon-blue)" stroke-width="3"/><path d="M26 50v10M33 50v10M40 50v10" stroke="var(--icon-blue)" stroke-width="2.5"/></svg>
    <p>Place the<br>order</p>
  </div>
  <div class="step" style="left:611px;top:140px">
    <svg width="76" height="102" viewBox="0 0 76 102"><rect x="2" y="22" width="44" height="78" rx="5" fill="var(--icon-blue)"/><rect x="8" y="34" width="32" height="52" fill="var(--pale)"/><circle cx="24" cy="93" r="3.5" fill="var(--pale)"/><path d="M50 20a14 14 0 0 1 10 10M50 10a24 24 0 0 1 20 20M50 0a34 34 0 0 1 24 24" fill="none" stroke="var(--icon-blue)" stroke-width="4"/></svg>
    <p>Get a callback within<br>the hour</p>
  </div>
  <div class="step" style="left:831px;top:140px">
    <svg width="56" height="102" viewBox="0 0 56 102"><rect x="2" y="2" width="52" height="98" rx="6" fill="var(--icon-blue)"/><rect x="8" y="16" width="40" height="66" fill="var(--pale)"/><circle cx="28" cy="91" r="4" fill="var(--pale)"/><path d="M28 28a11 11 0 0 0-11 11c0 8 11 19 11 19s11-11 11-19a11 11 0 0 0-11-11zm0 15a4 4 0 1 1 0-8 4 4 0 0 1 0 8z" fill="var(--icon-blue)"/></svg>
    <p>Set date and<br>location</p>
  </div>
  <div class="step" style="left:1052px;top:140px">
    <svg width="80" height="94" viewBox="0 0 80 94"><path d="M40 4L2 40h10v52h56V40h10z" fill="var(--icon-blue)"/><path d="M40 12L62 33V36" fill="none"/><rect x="32" y="60" width="16" height="32" fill="var(--pale)"/></svg>
    <p>We will come<br>to you</p>
  </div>

  <svg class="dash" style="left:228px" width="100" height="20" viewBox="0 0 100 20"><path d="M2 10h96" stroke="var(--orange)" stroke-width="2.5" stroke-dasharray="7 6"/><path d="M42 3l8 7-8 7" fill="none" stroke="var(--orange)" stroke-width="3"/></svg>
  <svg class="dash" style="left:451px" width="100" height="20" viewBox="0 0 100 20"><path d="M2 10h96" stroke="var(--orange)" stroke-width="2.5" stroke-dasharray="7 6"/><path d="M42 3l8 7-8 7" fill="none" stroke="var(--orange)" stroke-width="3"/></svg>
  <svg class="dash" style="left:671px" width="100" height="20" viewBox="0 0 100 20"><path d="M2 10h96" stroke="var(--orange)" stroke-width="2.5" stroke-dasharray="7 6"/><path d="M42 3l8 7-8 7" fill="none" stroke="var(--orange)" stroke-width="3"/></svg>
  <svg class="dash" style="left:891px" width="100" height="20" viewBox="0 0 100 20"><path d="M2 10h96" stroke="var(--orange)" stroke-width="2.5" stroke-dasharray="7 6"/><path d="M42 3l8 7-8 7" fill="none" stroke="var(--orange)" stroke-width="3"/></svg>
</section>

<div class="promo-photo" role="img" aria-label="Two repair engineers in blue work shirts with tool belts standing beside a white service van"></div>
<section class="promo">
  <h2>SAVE $100 ON HANDSET HAVEN<br>24/7 SUPPORT</h2>
  <p class="lead">Backed by a professional call center open 12 hours a day and open on a Saturday as well</p>
  <div class="perk" style="top:222px">
    <div class="perk-ring"><svg width="44" height="32" viewBox="0 0 44 32"><rect x="2" y="2" width="40" height="28" rx="3" fill="none" stroke="#fff" stroke-width="3"/><rect x="2" y="9" width="40" height="6" fill="#fff"/><rect x="8" y="21" width="12" height="3" fill="#fff"/></svg></div>
    <p>Get a Gift card for<br>your device</p>
  </div>
  <div class="perk" style="top:336px">
    <div class="perk-ring"><svg width="46" height="40" viewBox="0 0 46 40"><g fill="none" stroke="#fff" stroke-width="3.5"><circle cx="16" cy="22" r="8"/><circle cx="35" cy="11" r="5"/></g><g stroke="#fff" stroke-width="4"><path d="M16 8v5M16 31v5M2 22h5M25 22h5M6 12l3.5 3.5M22.5 28.5L26 32M6 32l3.5-3.5M22.5 15.5L26 12"/><path d="M35 1v4M35 17v4M25 11h4M41 11h4"/></g></svg></div>
    <p>Expert Service.<br>Unbeatable Price</p>
  </div>
</section>

<footer>
  <div class="footer-col" style="left:100px">
    <h3>Information</h3>
    <ul><li>About Us</li><li>Careers</li><li>Privacy &amp; Security</li><li>Site Map</li><li>Terms of Use</li><li>Blog</li></ul>
  </div>
  <div class="vline" style="left:271px"></div>
  <div class="footer-col" style="left:303px">
    <h3>Help &amp; support</h3>
    <ul><li>Login</li><li>New Customers</li><li>Products</li><li>Phone Repair</li><li>Frequently Asked Questions</li><li>How to Order</li></ul>
  </div>
  <div class="vline" style="left:508px"></div>
  <div class="footer-col" style="left:550px">
    <h3>My Account</h3>
    <ul><li>Delivery Information</li><li>My Account</li><li>Order Tracking</li><li>Reminder Service</li><li>Shipping, Returns &amp; Fees</li></ul>
  </div>
  <div class="vline" style="left:735px"></div>
  <div class="footer-col" style="left:777px">
    <h3>Email Subscription</h3>
    <p class="newsletter-note">Register your email address to get information about us</p>
    <div class="subscribe"><div class="field">Email Address</div><div class="btn">SUBSCRIBE</div></div>
    <h3 style="margin:16px 0 0">Stay Connected</h3>
    <div class="social">
      <i style="background:#3b5a9a"></i><i style="background:#4fb6e8"></i><i style="background:#dd4b39"></i><i style="background:#3f729b"></i><i style="background:#3fb5d8"></i><i style="background:#d92323"></i><i style="background:#c9202c"></i>
    </div>
  </div>
  <div class="copyright">Copyrights © 2017, Handset Haven. All Rights Reserved &nbsp;|&nbsp; Privacy Policy | Terms of Use | Feedback</div>
</footer>

</body>
</html>
```